Velk Partners Building Business Cards

We need a business card that reflects our business as "Solar Experts" in San Diego. Browse our website www.velkpartners.example our License needs to be displayed as "CSLB# 3867140" our phone number is (619) 555-0187

Save thousands on your electric bills and increase the value of your home while helping to protect the environment. Our solar installation experts will help you design the system that's right for you, using only the highest quality equipment that will look great and give you ideal performance. Our goal is to make you energy independent, and get your electric bill to 0.

Paul Osterby
(619) 555-0187
paul@velkpartners.example

Target Market(s)

Home owners in san diego looking for solar

Industry/Entity Type

Solar Energy

Contact Information for Business Card

Paul Osterby
(619) 555-0187
paul@velkpartners.example

Font styles to use
Other font styles liked:
• Use our logo font

Requirements
Must have
• License needs to be displayed as "CSLB# 3867140" our phone number is (619) 555-0187
Nice to have
• Real images of rooftop home solar in san diego
Should not have
• our business address

```html
<!DOCTYPE html>
<html lang="en">
<head>
<meta charset="utf-8">
<title>Velk Partners Building – Business Cards</title>
<link rel="stylesheet" href="https://fonts.googleapis.com/css2?family=Roboto:wght@400;700;900&family=Cinzel:wght@500&family=Tinos:ital@1&display=swap">
<style>
  :root {
    --navy: #1f3b77;
    --navy-deep: #1b3570;
    --sun: #f6b417;
    --paper: #ffffff;
    --ink: #4a4a4a;
    --backdrop: #e4e4e4;
  }
  * { margin: 0; padding: 0; box-sizing: border-box; }
  html, body { width: 1200px; height: 1000px; overflow: hidden; }
  body { background: var(--backdrop); position: relative; font-family: "Roboto", sans-serif; }

  .card {
    position: absolute;
    left: 220px;
    width: 760px;
    height: 434px;
    overflow: hidden;
    box-shadow: 0 2px 6px rgba(0,0,0,0.18);
  }

  /* Front */
  .card-front { top: 50px; background: var(--navy); color: var(--paper); }
  .front-name {
    position: absolute;
    top: 218px; left: 0; right: 0;
    text-align: center;
    font-family: "Roboto", sans-serif;
    font-weight: 900;
    font-size: 43px;
    letter-spacing: -0.5px;
    white-space: nowrap;
    color: var(--paper);
  }
  .front-tagline {
    position: absolute;
    top: 352px; left: 0; right: 0;
    text-align: center;
    font-family: "Tinos", serif;
    font-style: italic;
    font-size: 28px;
    letter-spacing: 0.5px;
    color: var(--paper);
  }

  /* Back */
  .card-back { top: 523px; height: 436px; background: var(--paper); }
  .back-name {
    position: absolute;
    top: 48px; left: 43px;
    font-family: "Roboto", sans-serif;
    font-weight: 900;
    font-size: 26px;
    letter-spacing: -0.3px;
    white-space: nowrap;
    color: var(--navy-deep);
  }
  .sun-art {
    position: absolute;
    top: 0; right: 0;
    width: 375px; height: 436px;
    background: linear-gradient(160deg, #ffffff 0%, #fbd36a 25%, var(--sun) 55%, #5f6f8a 78%, var(--navy) 100%);
  }
  .person {
    position: absolute;
    top: 258px; left: 43px;
    font-family: "Cinzel", serif;
    font-weight: 500;
    font-size: 23px;
    letter-spacing: 1px;
    color: var(--navy-deep);
  }
  .contacts { position: absolute; top: 305px; left: 43px; list-style: none; }
  .contacts li {
    display: flex; align-items: center;
    height: 24.5px;
    font-size: 17px;
    white-space: nowrap;
    color: var(--ink);
  }
  .contacts svg { width: 13px; height: 13px; margin-right: 7px; flex: none; }
</style>
</head>
<body>

<section class="card card-front">
  <div class="front-name">Velk Partners Building Inc</div>
  <div class="front-tagline">The Solar Experts</div>
</section>

<section class="card card-back">
  <div class="back-name">Velk Partners Building Inc</div>
  <div class="sun-art" role="img" aria-label="Large rising sun with rays over blue waves"></div>

  <div class="person">Paul Osterby</div>
  <ul class="contacts">
    <li>
      <svg viewBox="0 0 13 13" aria-hidden="true"><rect x="3.5" y="0.8" width="6" height="11.4" rx="1.2" fill="none" stroke="#f6b417" stroke-width="1.4"/><circle cx="6.5" cy="10" r="0.8" fill="#f6b417"/></svg>
      (619) 555-0187
    </li>
    <li>
      <svg viewBox="0 0 13 13" aria-hidden="true"><rect x="0.5" y="2.5" width="12" height="8" fill="#f6b417"/><path d="M0.8 2.8 L6.5 7.2 L12.2 2.8" fill="none" stroke="#fff" stroke-width="1"/></svg>
      paul@velkpartners.example
    </li>
    <li>
      <svg viewBox="0 0 13 13" aria-hidden="true"><circle cx="6.5" cy="6.5" r="5.8" fill="#f6b417"/><path d="M0.7 6.5h11.6M6.5 0.7v11.6M6.5 0.7c-3 3-3 8.6 0 11.6M6.5 0.7c3 3 3 8.6 0 11.6" fill="none" stroke="#fff" stroke-width="0.8"/></svg>
      www.velkpartners.example
    </li>
    <li>
      <svg viewBox="0 0 13 13" aria-hidden="true"><circle cx="6.5" cy="6.5" r="5.8" fill="#f6b417"/><path d="M3.6 6.8 L5.7 8.9 L9.6 4.4" fill="none" stroke="#fff" stroke-width="1.4"/></svg>
      CSLB# 3867140
    </li>
  </ul>
</section>

</body>
</html>
```